Firm-Asset: Tomorrow - EU-funded management consulting

A website to inform possible customers about my management consulting services for small and medium sized companies. I am using a funding for small and medium companies to do 10 days of workshops and coaching about leadership, further education and employee's health. The Funding is called "Betriebsgut Zukunft" which means something like: Humans are the value of the company. The official logo is attached as a

Target Market(s)

Small and medium sized companies that want to improve their employee's well being and efficiency.

Industry/Entity Type

Management Consulting

Contact Information for Business Card

Malte Quast, Birkenhainweg 14, 10219 Berlin

Logo Text

BetriebsGut Zukunft - Beratung

Font styles to use
Serif
Sans Serif

Requirements
Must have
• a friendly and professional design
Nice to have
• saying somthing about: employees, leadership, further education and employees health are important to us.
Should not have
• should not be too shimmering

```html
<!DOCTYPE html>
<html lang="en">
<head>
<meta charset="utf-8">
<title>Betriebsgut Zukunft – Consulting</title>
<link rel="stylesheet" href="https://fonts.googleapis.com/css2?family=Open+Sans:wght@400;600;700;800&display=swap">
<style>
:root{
  --blue:#1f5b8c;
  --blue-dark:#16476f;
  --orange:#d9832b;
  --orange-dark:#b86a1d;
  --ink:#2e3440;
  --muted:#7b8490;
  --line:#e3e6ea;
  --paper:#ffffff;
  --soft:#f4f5f7;
  --dark:#23272d;
}
*{box-sizing:border-box;margin:0;padding:0}
html,body{width:1200px;height:2296px;overflow:hidden}
body{font-family:"Open Sans",Arial,sans-serif;color:var(--ink);background:var(--paper);position:relative}

/* header */
.site-header{height:64px;display:flex;align-items:center;justify-content:space-between;padding:0 40px;border-bottom:1px solid var(--line)}
.brand{display:flex;align-items:center;gap:10px}
.brand-mark{width:34px;height:34px;background:var(--orange)}
.brand-name{font-weight:700;color:var(--blue);font-size:18px;line-height:1.05}
.brand-name small{display:block;font-weight:700;font-size:18px;color:var(--blue)}
.main-nav{display:flex}
.main-nav a{font-size:11px;font-weight:600;color:var(--ink);text-decoration:none;padding:8px 20px;letter-spacing:.5px}
.main-nav a.active{color:var(--blue)}

/* hero */
.hero{position:relative;height:590px;background:linear-gradient(180deg,#8d949c 0%,#6f7780 45%,#4d545c 100%)}
.hero-photo{position:absolute;inset:0;background:radial-gradient(ellipse at 50% 35%,rgba(255,255,255,.25),transparent 60%)}
.hero-content{position:absolute;left:0;right:0;top:230px;text-align:center;color:#fff}
.hero-title{font-size:44px;font-weight:800;letter-spacing:1px}
.hero-text{font-size:20px;line-height:1.4;width:720px;margin:14px auto 0}
.btn{display:inline-block;background:var(--orange);color:#fff;font-size:11px;font-weight:700;padding:12px 26px;border-radius:2px;letter-spacing:.6px}
.hero .btn{margin-top:22px}

/* welcome */
.welcome{padding:70px 0 0;text-align:center}
.section-title{font-size:25px;font-weight:700;color:var(--blue);letter-spacing:.5px}
.section-rule{width:70px;height:3px;background:var(--orange);margin:12px auto 0}
.lead{width:1020px;margin:22px auto 0;font-size:12px;line-height:1.6;color:var(--muted);height:58px}
.features{display:flex;gap:28px;width:1060px;margin:50px auto 0}
.feature{flex:1;background:var(--soft);border:1px solid var(--line);border-top:4px solid var(--orange);padding:30px 20px 28px;height:280px;position:relative}
.feature-icon{width:62px;height:62px;border-radius:50%;background:var(--blue);margin:0 auto;display:flex;align-items:center;justify-content:center}
.feature h3{margin-top:20px;font-size:14px;font-weight:700;color:var(--blue);line-height:1.3;height:38px}
.feature p{font-size:11px;line-height:1.6;color:var(--muted);margin-top:14px}
.feature .more{position:absolute;right:16px;bottom:14px;width:10px;height:10px;border-radius:50%;border:1px solid var(--muted)}

/* about + faq */
.about{display:flex;width:1080px;margin:60px auto 0;height:420px}
.about-photo{width:210px;height:400px;background:linear-gradient(180deg,#d7dbe0,#9aa2ab);border-radius:2px}
.about-body{width:460px;margin-left:30px;padding-top:40px}
.about-body h2{font-size:30px;font-weight:800;color:var(--ink);line-height:1}
.about-body h2 span{display:block;font-size:18px;color:var(--blue);margin-top:4px}
.about-body .section-rule{margin:12px 0 0}
.about-body p{font-size:12px;line-height:1.7;color:var(--muted);margin-top:18px}
.about-body .btn{margin-top:22px}
.faq{width:350px;margin-left:30px;padding-top:10px}
.faq h2{font-size:26px;font-weight:700;color:var(--blue)}
.faq .section-rule{margin:10px 0 18px}
.faq-item{border:1px solid var(--line);margin-bottom:8px}
.faq-q{background:var(--soft);font-size:11px;color:var(--blue);padding:9px 12px;font-weight:600;display:flex;justify-content:space-between}
.faq-q b{color:var(--orange)}
.faq-a{font-size:11px;color:var(--muted);padding:10px 12px;line-height:1.6}

/* testimonials */
.testimonials{position:relative;height:250px;margin-top:10px;background:linear-gradient(180deg,#3a3f46,#22262b);color:#fff;text-align:center}
.testimonials .section-title{color:#fff;padding-top:24px}
.testimonials .section-rule{margin-top:10px}
.quote{width:860px;margin:22px auto 0;font-size:12px;line-height:1.7;color:#dfe3e7;position:relative}
.quote::before{content:"\201C";position:absolute;left:-30px;top:-14px;font-size:44px;color:#fff}
.quote::after{content:"\201D";position:absolute;right:-30px;top:-14px;font-size:44px;color:#fff}
.reviewer{display:flex;align-items:center;justify-content:center;gap:14px;margin-top:16px}
.reviewer-photo{width:56px;height:56px;border-radius:50%;background:linear-gradient(180deg,#c9ccd1,#8b9097);border:3px solid #fff}
.reviewer-name{text-align:left;font-size:12px;font-weight:700}
.reviewer-name small{display:block;font-weight:400;color:#bfc4ca;font-size:11px}

/* clients */
.clients{display:flex;justify-content:space-between;align-items:center;width:1100px;height:100px;margin:0 auto}
.client{font-size:17px;font-weight:700;color:#6f7781;display:flex;align-items:center;gap:6px}
.client i{width:12px;height:12px;background:#9aa2ab;display:inline-block}

/* footer */
.site-footer{position:absolute;left:0;right:0;top:2030px;height:230px;background:var(--soft);border-top:1px solid var(--line);display:flex;padding:28px 0 0 90px}
.footer-brand{width:240px}
.footer-col{width:220px}
.footer-col h4{font-size:12px;font-weight:700;color:var(--ink);letter-spacing:.5px}
.footer-col .section-rule{margin:6px 0 12px;width:30px;height:2px}
.footer-col li{list-style:none;font-size:10px;color:var(--muted);line-height:1.75;display:flex;align-items:center;gap:8px}
.social-dot{width:14px;height:14px;border-radius:50%;background:var(--blue);display:inline-block}
.copyright{position:absolute;left:0;right:0;bottom:0;height:36px;background:var(--dark);color:#9aa0a7;font-size:10px;display:flex;align-items:center;justify-content:center}
</style>
</head>
<body>

<header class="site-header">
  <div class="brand">
    <span class="brand-mark"></span>
    <div class="brand-name">Betriebsgut<small>Zukunft</small></div>
  </div>
  <nav class="main-nav">
    <a class="active">HOME</a><a>ABOUT US</a><a>SERVICES</a><a>TESTIMONIALS</a><a>CLIENTS</a><a>CONTACT US</a>
  </nav>
</header>

<section class="hero">
  <div class="hero-photo" role="img" aria-label="Photo of a business team meeting around a conference table"></div>
  <div class="hero-content">
    <h1 class="hero-title">BETRIEBSGUT: ZUKUNFT</h1>
    <p class="hero-text">We offer services to small and medium sized companies and conduct workshops on leadership, employee health and further education.</p>
    <span class="btn">READ MORE INFO</span>
  </div>
</section>

<section class="welcome">
  <h2 class="section-title">WELCOME TO BETRIEBSGUT: ZUKUNFT</h2>
  <div class="section-rule"></div>
  <p class="lead">We support small and medium sized companies with ten days of funded workshops and coaching. Together we strengthen leadership, keep your team healthy and open new paths of learning, because people are the true value of every company. Our approach is practical, personal and made to fit the daily life of your business and your employees.</p>

  <div class="features">
    <div class="feature">
      <div class="feature-icon"><svg width="30" height="30" viewBox="0 0 30 30"><rect x="6" y="6" width="18" height="20" fill="#fff"/><rect x="10" y="10" width="3" height="3" fill="#1f5b8c"/><rect x="17" y="10" width="3" height="3" fill="#1f5b8c"/><rect x="10" y="16" width="3" height="3" fill="#1f5b8c"/><rect x="17" y="16" width="3" height="3" fill="#1f5b8c"/><rect x="13" y="21" width="4" height="5" fill="#1f5b8c"/></svg></div>
      <h3>SMALL AND MEDIUM<br>SIZED COMPANIES</h3>
      <p>Tailored consulting for growing firms that want to invest in their people and their future.</p>
      <span class="more"></span>
    </div>
    <div class="feature">
      <div class="feature-icon"><svg width="32" height="30" viewBox="0 0 32 30"><polygon points="16,6 30,12 16,18 2,12" fill="#fff"/><path d="M8 15v6c0 2 4 4 8 4s8-2 8-4v-6l-8 3z" fill="#fff"/></svg></div>
      <h3>WORKSHOPS ON<br>LEADERSHIP</h3>
      <p>Hands-on sessions that help managers lead with clarity, trust and a steady voice.</p>
      <span class="more"></span>
    </div>
    <div class="feature">
      <div class="feature-icon"><svg width="30" height="30" viewBox="0 0 30 30"><circle cx="15" cy="10" r="5" fill="#fff"/><path d="M5 26c0-6 4-9 10-9s10 3 10 9z" fill="#fff"/></svg></div>
      <h3>EMPLOYEES<br>HEALTH</h3>
      <p>Practical steps for a healthy workplace, less stress and more energy in every team.</p>
      <span class="more"></span>
    </div>
    <div class="feature">
      <div class="feature-icon"><svg width="30" height="30" viewBox="0 0 30 30"><path d="M3 8c4-2 8-2 12 1v15c-4-3-8-3-12-1z" fill="#fff"/><path d="M27 8c-4-2-8-2-12 1v15c4-3 8-3 12-1z" fill="#fff"/></svg></div>
      <h3>FURTHER<br>EDUCATION</h3>
      <p>Learning plans that keep skills fresh and open new chances for your employees.</p>
      <span class="more"></span>
    </div>
  </div>
</section>

<section class="about">
  <div class="about-photo" role="img" aria-label="Photo of a consultant in a suit"></div>
  <div class="about-body">
    <h2>ABOUT<span>BETRIEBSGUT: ZUKUNFT</span></h2>
    <div class="section-rule"></div>
    <p>Malte Quast is a management consultant based in Berlin. With the funding programme Betriebsgut Zukunft he helps companies turn good intentions into lasting change. Every project starts with listening and ends with clear steps your team can carry on alone.</p>
    <p>From the first talk to the final coaching day, you work with one partner who knows your goals.</p>
    <span class="btn">READ MORE INFO</span>
  </div>
  <div class="faq">
    <h2>FAQ'S</h2>
    <div class="section-rule"></div>
    <div class="faq-item"><div class="faq-q">Who can apply for the funding? <b>–</b></div><div class="faq-a">Small and medium sized companies with up to 249 employees based in Germany.</div></div>
    <div class="faq-item"><div class="faq-q">How many days are covered? <b>+</b></div></div>
    <div class="faq-item"><div class="faq-q">What topics can we choose? <b>+</b></div></div>
    <div class="faq-item"><div class="faq-q">How do we get started? <b>+</b></div></div>
  </div>
</section>

<section class="testimonials" role="img" aria-label="Dimmed photo of colleagues in an office behind the testimonials">
  <h2 class="section-title">TESTIMONIALS</h2>
  <div class="section-rule"></div>
  <p class="quote">The workshops gave our team a shared language for leadership and a real plan for health at work. Malte listened first, then guided us with calm and clear advice. Six months later we still use the tools every week, and our staff feel more valued than ever before.</p>
  <div class="reviewer">
    <div class="reviewer-photo" role="img" aria-label="Portrait of the reviewer"></div>
    <div class="reviewer-name">Lena Hartwig<small>Managing Director</small></div>
  </div>
</section>

<section class="clients">
  <span class="client"><i></i>Nordwerk</span>
  <span class="client"><i></i>Groupe Lumen</span>
  <span class="client"><i></i>Tessera</span>
  <span class="client"><i></i>Wolkenhaus</span>
  <span class="client"><i></i>Sankt Auen</span>
  <span class="client"><i></i>Ortalis</span>
  <span class="client"><i></i>Feldmarke</span>
</section>

<footer class="site-footer">
  <div class="footer-brand">
    <div class="brand"><span class="brand-mark"></span><div class="brand-name">Betriebsgut<small>Zukunft</small></div></div>
  </div>
  <div class="footer-col">
    <h4>WELCOME</h4><div class="section-rule"></div>
    <ul><li>Home</li><li>About us</li><li>Services</li><li>Testimonials</li><li>Clients</li><li>Contact us</li></ul>
  </div>
  <div class="footer-col">
    <h4>CONTACT</h4><div class="section-rule"></div>
    <ul><li>Malte Quast</li><li>Birkenhainweg 14</li><li>10219 Berlin</li><li>+49 30 5550 1427</li><li>kontakt@betriebsgut-zukunft.example</li></ul>
  </div>
  <div class="footer-col">
    <h4>INFORMATION</h4><div class="section-rule"></div>
    <ul><li>Privacy policy</li><li>Terms &amp; conditions</li><li>Imprint</li></ul>
  </div>
  <div class="footer-col">
    <h4>FOLLOW US</h4><div class="section-rule"></div>
    <ul><li><span class="social-dot"></span>Network</li><li><span class="social-dot"></span>Updates</li><li><span class="social-dot"></span>Profile</li></ul>
  </div>
</footer>
<div class="copyright">© 2024 Betriebsgut Zukunft – Beratung. All rights reserved.</div>

</body>
</html>
```